Lumen Fitness Personal Training Business

I need a business card design with a logo for my personal training company. I'd like the colors to be a vibrant green and black. I'd like the logo to incorporate an anvil (or something similar). I train hardcore competitive athletes as well as soccer moms trying to get and/or stay in shape. I need a logo that will not pigeon hole me in one category or the other, but at the same time not be too intimidating to soccer moms, but will not be off putting to the more hardcore trainees. The design should be attention grabbing and aesthetic.
Target Market(s)
Hardcore athletes as well as average people just trying to get/stay in shape.
Industry/Entity Type
Training

```html
<!DOCTYPE html>
<html lang="en">
<head>
<meta charset="utf-8">
<title>Lumen Fitness – Business Card</title>
<link rel="stylesheet" href="https://fonts.googleapis.com/css2?family=Lato:wght@400;700;900&display=swap">
<style>
  :root {
    --backdrop: #2b2b2b;
    --card: #141414;
    --card-edge: #1c1c1c;
    --green: #2fbf4a;
    --green-bright: #3fd95a;
    --text-light: #e9e9e9;
    --muted-grey: #5b5b5b;
  }
  * { box-sizing: border-box; margin: 0; padding: 0; }
  html, body {
    width: 1200px; height: 900px; overflow: hidden;
    background: var(--backdrop);
    font-family: "Lato", Arial, sans-serif;
  }
  .stage {
    position: relative; width: 1200px; height: 900px;
    display: flex; align-items: center; justify-content: center; gap: 50px;
  }
  .card {
    position: relative;
    width: 500px; height: 286px;
    border-radius: 22px;
    background: var(--card);
    box-shadow: 0 0 0 1px var(--card-edge);
    overflow: hidden;
  }
  /* Front */
  .card-front { display: flex; }
  .brand-block {
    width: 52%;
    display: flex; align-items: center; justify-content: center; gap: 12px;
  }
  .brand-square {
    width: 22px; height: 22px; background: var(--green);
  }
  .brand-name {
    font-weight: 900; font-size: 30px; letter-spacing: 0.5px;
    color: var(--green); text-transform: uppercase; line-height: 1;
  }
  .contact-block {
    width: 48%;
    padding: 56px 20px 0 4px;
    color: var(--text-light);
    font-size: 14px; line-height: 1.35;
  }
  .person-name { color: var(--green-bright); font-size: 21px; font-weight: 400; }
  .person-role { font-size: 13px; margin-bottom: 14px; }
  .address { margin-bottom: 14px; }
  .contact-line .label { color: var(--green-bright); margin-right: 4px; }
  /* Back */
  .card-back {
    display: flex; align-items: center; justify-content: center;
  }
  .back-name {
    font-weight: 900; font-size: 38px; color: var(--muted-grey);
    text-transform: uppercase; letter-spacing: 0.5px;
  }
</style>
</head>
<body>
<main class="stage">
  <section class="card card-front" aria-label="Business card front">
    <div class="brand-block">
      <span class="brand-square" aria-hidden="true"></span>
      <span class="brand-name">Lumen Fitness</span>
    </div>
    <div class="contact-block">
      <p class="person-name">Daniel Hart</p>
      <p class="person-role">Managing Director</p>
      <p class="address">48 Harrow Lane<br>Brookfield, 560274.</p>
      <p class="contact-line"><span class="label">T:</span>044-555 018 260</p>
      <p class="contact-line"><span class="label">E:</span>hello@lumenfit.co</p>
      <p class="contact-line"><span class="label">W:</span>www.lumenfit.co</p>
    </div>
  </section>
  <section class="card card-back" aria-label="Business card back">
    <span class="back-name">Lumen Fitness</span>
  </section>
</main>
</body>
</html>
```